1. Overview of company:
Teal Q Amber Mobile solutions private Ltd is one of the leading innovators & providers of Value added services (VAS) and telecom solutions to the top telecom operators across the world. We are the pioneer of several telecom technologies and products with our solutions empowering over 40 telecom giant in 51 countries.

2. Product Overview:
Zippy tone is the most innovative voice morphing mobile app that has revolutionized the concept of IVR based offerings for telecom operators across the world. It lets you talk to your friend in a voice of your choice at just the press of a button. In addition to every call, users can now speak to their friends with background sounds of their choice.

In simple words: If person A calls person B, person A can choose the voice he wants B to listen, Words and sentences remain same just the voice changes. Person A can even activate a background sound for both of them while talking.

3. Objective of the design:
The purpose of this campaign is to establish Zippy tone as Innovative, Lively, Youthful, Fun mobile app generally used for spreading smiles via pranks. The primary objective is to persuade the audience to download and use Zippy Tone mobile app, as well as to spread and characterize this new app.

4. Product layout:
Page 1: Landing Page
- pictorial explanation, what Zippy Tone stands for

Page 2: Home Screen options
-Navigation to zippy tone
-Navigation to zippy backdrop

Page 3: Zippy Tone options
-Female
-Cartoon
-King
-Bunny

Page 4: Zippy backdrop options
-Romantic
-Airport
-Traffic
-Football
-Church
-Beach

5. Target Audience
The users of the mobile app will be teenager whose age ranges from 16-27. The demographics are not restricted to a particular country and will be present on global level.

6. Deliverable
- 4 Uncoded screen and icon for mobile app "Zippy Tone"
- Our company name is "Teal Q amber" , we would like to see designs that use Black and Green, at the same time its not mandatory.
-Design should communicate what the app stands for "Changing voice of caller"

Target Market(s)

User of the mobile app will be teenagers whose age ranges from 16-27. The demographics are not restricted to a particular country and will be present on global level. It's for masses.

Industry/Entity Type

Telecommunications

Requirements
Must have
• The design should be self explanatory, what the app stands for.
• Editable format for integration purpose.
Nice to have
• Would prefer Icons and very few words.
• Professional, elegant at the same time trendy designs.

```html
<!DOCTYPE html>
<html lang="en">
<head>
<meta charset="utf-8">
<title>Zippy Tone options</title>
<link rel="stylesheet" href="https://fonts.googleapis.com/css2?family=Patrick+Hand&family=Questrial&display=swap">
<style>
  :root {
    --green: #95c13d;
    --band: #ededed;
    --ink: #555555;
    --muted: #a9a9a9;
    --rule: #bdbdbd;
    --white: #ffffff;
    --amber: #f5b031;
    --charcoal: #5a5a5a;
    --pink: #f4b6c6;
  }
  * { margin: 0; padding: 0; box-sizing: border-box; }
  html, body { width: 675px; height: 1200px; overflow: hidden; background: var(--white); }
  .screen { position: relative; width: 675px; height: 1200px; background: var(--white); overflow: hidden; }

  .header-bg { position: absolute; left: 0; top: 0; width: 675px; height: 210px; }
  .back-button { position: absolute; left: 36px; top: 70px; width: 36px; height: 40px; }
  .screen-title {
    position: absolute; left: 0; right: 0; top: 52px; text-align: center;
    font-family: "Patrick Hand", cursive; font-size: 48px; color: var(--white);
    letter-spacing: 1px; word-spacing: 10px;
  }
  .screen-subtitle {
    position: absolute; left: 0; right: 0; top: 157px; text-align: center;
    font-family: "Questrial", sans-serif; font-size: 25px; color: var(--muted);
  }

  .voice-list { position: absolute; left: 0; top: 336px; width: 675px; list-style: none; }
  .voice-option { position: relative; height: 124px; }
  .voice-option + .voice-option { border-top: 1.5px solid var(--rule); }
  .voice-icon { position: absolute; left: 40px; top: 16px; width: 98px; height: 92px; border-radius: 14px; }
  .icon-female { background: var(--amber); }
  .icon-cartoon { background: var(--charcoal); }
  .icon-king { background: var(--amber); height: 70px; top: 28px; }
  .icon-bunny { background: linear-gradient(90deg, #e8e8e8, var(--pink), #e8e8e8); }
  .voice-label {
    position: absolute; left: 190px; top: 30px;
    font-family: "Patrick Hand", cursive; font-size: 50px; color: var(--ink); line-height: 1.2;
  }
  .radio { position: absolute; left: 582px; top: 36px; width: 54px; height: 54px; }

  .save-button { position: absolute; left: 222px; top: 1010px; width: 232px; height: 74px; }
  .save-button span {
    position: absolute; inset: 0; display: flex; align-items: center; justify-content: center;
    font-family: "Patrick Hand", cursive; font-size: 50px; color: var(--white); letter-spacing: 1px;
  }
</style>
</head>
<body>
<main class="screen">
  <svg class="header-bg" viewBox="0 0 675 210" aria-hidden="true">
    <path d="M0 140 Q170 122 340 138 T675 140 L675 198 Q500 192 340 196 T0 200 Z" fill="var(--band)"/>
    <path d="M0 0 H675 V146 Q520 136 340 144 T0 148 Z" fill="var(--green)"/>
  </svg>
  <svg class="back-button" viewBox="0 0 36 40" aria-label="Back">
    <path d="M30 6 L8 20 L30 34" fill="none" stroke="var(--white)" stroke-width="6" stroke-linecap="round" stroke-linejoin="round"/>
  </svg>
  <h1 class="screen-title">Zippy Tone options</h1>
  <p class="screen-subtitle">select the voice that you want to talk</p>

  <ul class="voice-list">
    <li class="voice-option">
      <div class="voice-icon icon-female" role="img" aria-label="Icon of a woman with orange hair"></div>
      <span class="voice-label">Female</span>
      <svg class="radio" viewBox="0 0 54 54"><circle cx="27" cy="27" r="24" fill="none" stroke="var(--green)" stroke-width="3"/></svg>
    </li>
    <li class="voice-option">
      <div class="voice-icon icon-cartoon" role="img" aria-label="Icon of a cartoon character head"></div>
      <span class="voice-label">Cartoon</span>
      <svg class="radio" viewBox="0 0 54 54"><circle cx="27" cy="27" r="24" fill="none" stroke="var(--green)" stroke-width="3"/><circle cx="27" cy="27" r="18" fill="var(--green)"/></svg>
    </li>
    <li class="voice-option">
      <div class="voice-icon icon-king" role="img" aria-label="Icon of an orange crown"></div>
      <span class="voice-label">King</span>
      <svg class="radio" viewBox="0 0 54 54"><circle cx="27" cy="27" r="24" fill="none" stroke="var(--green)" stroke-width="3"/></svg>
    </li>
    <li class="voice-option">
      <div class="voice-icon icon-bunny" role="img" aria-label="Icon of bunny ears"></div>
      <span class="voice-label">Bunny</span>
      <svg class="radio" viewBox="0 0 54 54"><circle cx="27" cy="27" r="24" fill="none" stroke="var(--green)" stroke-width="3"/></svg>
    </li>
  </ul>

  <div class="save-button">
    <svg viewBox="0 0 232 74" width="232" height="74" aria-hidden="true">
      <path d="M6 6 Q116 0 226 4 Q232 36 228 70 Q116 74 8 72 Q0 38 6 6 Z" fill="var(--green)"/>
    </svg>
    <span>SAVE</span>
  </div>
</main>
</body>
</html>
```